Dog Snacks brand needs a new packaging design

Dear Designers,

We are looking for a packaging expert to design our new line of Dog Snacks which contain a relaxing hemp extract (CBD).

Our company is already selling various relaxing cat & dog products , and we would like this new design to reflect the same "style & feeling" as our current products (see attached instructions).

Technical aspects:
- The packaging is a Stand Up Pouch (12x18.5x7cm - see attached instructions).
- Please follow technical guidelines from printer (see attached instructions).
- The packaging will contain 120g of high-quality, semi-moist dog snacks.
- We will be designing 3 differents variations for 3 different flavours: Chicken, Beef & Liver.
- The packaging will be printed with a matt finish.

Design aspects:
- The design should be compatible with our brand identity (i.e. fluffly, pure, relaxing, positive, clean & natural).
- Soft/rounded shapes are preferred.
- Please use our brand's colors (#3BA384, White & Black).
- Please use our company logo (see attached instructions).
- The design also needs to convey a strong sense of professionalism as we are an animal "healthcare" brand.
- If you want to include a dog picture, we would prefer you to use a picture of our official brand ambassador (see attached instructions).
- We have attached a number of packaging examples which we like a lot. (see attached instructions). Please only use those as general inspiration.
- Only original work (no plagiarism will be accepted).

Please don't hesitate to send us a message if you have any questions about the brand, the product or the design requirements.

We look forward to seeing your designs & working on this together !

Thanks & regards,
Tobias

Target Market(s)

Dog owners

Industry/Entity Type

Pet Care

Font styles to use
Sans Serif

Requirements
Must have
• Please see project description.
Nice to have
Should not have

```html
<!DOCTYPE html>
<html lang="en">
<head>
<meta charset="utf-8">
<title>Verdalis CalmBites CBD Treats – Chicken Pouch</title>
<link rel="stylesheet" href="https://fonts.googleapis.com/css2?family=Arvo:wght@400;700&family=Montserrat:wght@500;600;700&display=swap">
<style>
  :root{
    --backdrop:#1c2d27;
    --pouch-light:#f1f2f2;
    --pouch-mid:#d9dbdb;
    --brand-green:#2f8f70;
    --brand-green-light:#3ba384;
    --ink:#1b2620;
    --white:#ffffff;
    --photo-a:#b9b5b6;
    --photo-b:#8f8a8d;
  }
  *{box-sizing:border-box;margin:0;padding:0}
  html,body{width:1200px;height:960px;overflow:hidden}
  body{background:var(--backdrop);position:relative;font-family:"Montserrat",sans-serif}

  .pouch{
    position:absolute;left:320px;top:45px;width:560px;height:870px;
    border-radius:34px 34px 6px 6px;
    background:linear-gradient(100deg,var(--pouch-mid) 0%,var(--pouch-light) 40%,var(--pouch-light) 60%,var(--pouch-mid) 100%);
    overflow:hidden;
  }
  .zip-line{position:absolute;left:24px;right:24px;top:154px;height:2px;background:#c4c6c6}

  .brand-dot{position:absolute;left:250px;top:200px;width:60px;height:60px;border-radius:50%;border:4px solid var(--brand-green)}
  .brand-name{position:absolute;left:0;right:0;top:283px;text-align:center;font-family:"Arvo",serif;font-weight:700;font-size:56px;letter-spacing:1px;color:var(--ink);line-height:1}
  .brand-sub{position:absolute;right:115px;top:345px;font-family:"Arvo",serif;font-size:23px;color:var(--brand-green);line-height:1}

  .product-name{position:absolute;left:0;right:0;top:380px;text-align:center;font-weight:600;font-size:38px;font-variant:small-caps;letter-spacing:1px;color:var(--brand-green);line-height:1}
  .product-name sup{font-size:12px;vertical-align:top;position:relative;top:4px}
  .product-type{position:absolute;left:0;right:0;top:422px;text-align:center;font-weight:600;font-size:32px;letter-spacing:2px;color:var(--ink);line-height:1}

  .dose-pill{position:absolute;left:151px;top:463px;width:260px;height:23px;border-radius:4px;background:var(--brand-green);color:var(--white);font-size:15px;font-weight:600;letter-spacing:1px;display:flex;align-items:center;justify-content:center;gap:8px}
  .dose-pill .divider{width:1.5px;height:15px;background:var(--white)}
  .benefits{position:absolute;left:0;right:0;top:505px;text-align:center;font-size:13px;font-weight:600;letter-spacing:1px;color:var(--ink)}

  .flavour-badge{position:absolute;left:82px;top:567px;width:176px;height:176px;border-radius:50%;background:radial-gradient(circle at 40% 35%,var(--brand-green-light),var(--brand-green));display:flex;flex-direction:column;align-items:center;justify-content:flex-end;padding-bottom:34px;color:var(--white)}
  .flavour-badge::before{content:"";position:absolute;inset:8px;border-radius:50%;border:1.5px dashed rgba(255,255,255,.8)}
  .flavour-name{font-size:19px;font-weight:700;letter-spacing:1.5px}
  .flavour-rule{width:70px;height:1px;background:rgba(255,255,255,.8);margin:6px 0 4px}
  .flavour-weight{font-size:18px;font-weight:500;letter-spacing:1px}

  .endorsement{position:absolute;left:82px;top:742px;font-size:12.5px;color:var(--ink);line-height:1.1;letter-spacing:.5px}
  .endorsement .lead{font-variant:small-caps;font-size:14px;font-weight:500}
  .endorsement .strong{font-weight:700}

  .ambassador-photo{position:absolute;left:262px;top:513px;width:298px;height:292px;border-radius:46% 54% 0 0/40% 40% 0 0;background:radial-gradient(ellipse at 45% 40%,var(--photo-a),var(--photo-b))}

  .base-band{position:absolute;left:0;right:0;bottom:0;height:67px;background:var(--brand-green)}
</style>
</head>
<body>
  <main class="pouch">
    <div class="zip-line"></div>

    <div class="brand-dot"></div>
    <h1 class="brand-name">VERDALIS</h1>
    <p class="brand-sub">For Animals</p>

    <h2 class="product-name">CalmBites<sup>™</sup></h2>
    <p class="product-type">CBD TREATS</p>

    <div class="dose-pill"><span>CBD 250MG</span><span class="divider"></span><span>0% THC</span></div>
    <p class="benefits">SUPPORT | CALM | EASE</p>

    <div class="ambassador-photo" role="img" aria-label="Photo of the brand's ambassador dog, a wrinkly light-grey shar-pei looking up"></div>

    <div class="flavour-badge">
      <span class="flavour-name">CHICKEN</span>
      <span class="flavour-rule"></span>
      <span class="flavour-weight">120G</span>
    </div>

    <p class="endorsement"><span class="lead">Recommended by</span><br><span class="strong">VETERINARIANS</span></p>

    <div class="base-band"></div>
  </main>
</body>
</html>
```